Chorefinch clone for Asia

I am developing a clone for www.chorefinchly.example. It is meant for Asia (i.e. Singapore, Australia, Indonesian, Philippines, Malaysia).

I need a webdesign that functionally look like chorefinch, but localised with pictures of Asian of multi country (rather than latin american looks).

The color, iconography, images can be different, but the functionality must be all be similar to www.chorefinchly.example

I need a mobile UI as well that is for a mobile app, again, similar to that of chorefinch mobile app.

Note that I need the design for the following pages:
1. homepage
2. login page
3. page after login in.
4. search page & results
5. post a task & confirmation page
6. Payment page
7. User Review page.
8. Sign up page.

The webpages are to be in english....

The features must have photos of friendly looking helpers.

Target Market(s)

Asian countries. To serve a mass market, for part time, one off task job.

Requirements
Must have
• Just use ChoreFinchAsia for the name of the site for Starters. I have not arrived at a name yet.

```html
<!DOCTYPE html>
<html lang="en">
<head>
<meta charset="utf-8">
<title>Kerjaloo — Get just about anything done</title>
<link href="https://fonts.googleapis.com/css2?family=Ubuntu:wght@400;500;700&family=Arimo:wght@400;700&display=swap" rel="stylesheet">
<style>
:root{
  --ink-dark:#0b1c2c;
  --header-top:#0d2a47;
  --header-bottom:#1b4a73;
  --navy-text:#0f2c4a;
  --heading-blue:#3a5f86;
  --body-blue:#1f4a7a;
  --green:#7fb43a;
  --green-dark:#5f9a1e;
  --soft-green:#8aac55;
  --white:#ffffff;
  --footer-bg:#ebe9e9;
  --footer-text:#333333;
  --link-blue:#3d6aa0;
  --line-grey:#cfcfcf;
  --dot-red:#c8475d;
  --dot-slate:#3c4b5c;
}
*{box-sizing:border-box;margin:0;padding:0}
html,body{width:1200px;height:1002px;overflow:hidden}
body{position:relative;background:var(--white);font-family:"Arimo",Arial,sans-serif;color:var(--footer-text)}
a{text-decoration:none;color:inherit}

.top-bar{position:absolute;left:0;top:0;width:1200px;height:42px;background:var(--ink-dark);border-bottom:1px solid #1c3a57}
.social-button{position:absolute;top:8px;height:26px;border-radius:4px;background:linear-gradient(#f6f6f6,#d9d9d9);font:700 11px "Ubuntu",sans-serif;color:#555;display:flex;align-items:center;padding:0 8px;gap:5px;white-space:nowrap}
.social-button .brand{color:#2b7bc0;font-size:12px}
.follow-button{left:88px;width:160px}
.connect-button{left:258px;width:152px}
.search-field{position:absolute;left:916px;top:8px;width:194px;height:28px;border-radius:14px;background:linear-gradient(#2a4c6c,#1a3550);border:1px solid #3d5d7b;color:var(--white);font:500 13px "Ubuntu",sans-serif;padding:6px 14px}
.search-field svg{position:absolute;right:12px;top:5px}

.site-header{position:absolute;left:0;top:43px;width:1200px;height:83px;background:linear-gradient(var(--header-top),var(--header-bottom))}
.wordmark{position:absolute;left:90px;top:20px;display:flex;align-items:center;gap:14px;font:700 34px "Ubuntu",sans-serif;color:var(--white)}
.wordmark-dot{width:40px;height:40px;border-radius:50%;background:var(--green)}
.tagline{position:absolute;left:607px;top:8px;width:490px;font:500 16.5px "Ubuntu",sans-serif;letter-spacing:-0.2px;color:var(--white);white-space:nowrap}
.email-input{position:absolute;left:609px;top:37px;width:375px;height:33px;background:var(--white);font:400 17px "Ubuntu",sans-serif;color:#9a9a9a;padding:7px 10px}
.start-button{position:absolute;left:997px;top:36px;width:115px;height:35px;border-radius:3px;background:linear-gradient(var(--green),var(--green-dark));font:700 16px "Ubuntu",sans-serif;color:var(--white);text-align:center;line-height:35px}

.main-nav{position:absolute;left:0;top:126px;width:1200px;height:49px;background:linear-gradient(#ffffff,#d8d8d8)}
.nav-item{position:absolute;top:0;height:49px;line-height:49px;font:500 13.5px "Ubuntu",sans-serif;letter-spacing:-0.3px;color:var(--navy-text);white-space:nowrap}
.nav-item.current{left:88px;width:138px;padding-left:16px;background:#efefef}
.nav-sep{position:absolute;top:0;line-height:49px;font:500 14px "Ubuntu",sans-serif;color:var(--navy-text)}
.help-button,.tell-button{position:absolute;top:7px;height:34px;border-radius:4px;display:flex;align-items:center;gap:8px;font:500 14px "Ubuntu",sans-serif;color:var(--white);padding-left:7px;white-space:nowrap}
.help-button{left:853px;width:94px;background:var(--ink-dark)}
.tell-button{left:959px;width:154px;background:linear-gradient(#76ab2f,#4f8a14)}

.hero-photo{position:absolute;left:88px;top:194px;width:708px;height:351px;border:1px solid #aaa;border-radius:4px;background:linear-gradient(100deg,#c8b9ad 0%,#b27d6a 30%,#d9c3b2 55%,#6a85a8 85%,#8aa8c9 100%)}
.slider-dots{position:absolute;left:0;bottom:0;width:83px;height:31px;background:var(--white);display:flex;gap:3px;align-items:center;padding-left:4px}
.slider-dots span{width:13px;height:13px;border-radius:50%;background:var(--dot-slate)}
.slider-dots span:first-child{background:var(--dot-red)}

.browse-panel{position:absolute;left:812px;top:192px;width:301px;height:354px;border:1px solid #ccc;border-radius:6px;background:linear-gradient(160deg,#f4f4f4,#e4e4e4);box-shadow:0 1px 3px rgba(0,0,0,.2)}
.browse-panel h2{font:500 18px "Ubuntu",sans-serif;color:var(--navy-text);margin:17px 0 0 24px}
.task-list{list-style:none;margin-top:13px}
.task-list li{height:30px;border-bottom:1px solid var(--line-grey);font:700 14px "Arimo",sans-serif;color:#4a4a4a;padding:5px 0 0 25px}
.task-list li:last-child{border-bottom:none}

.feature{position:absolute;top:570px}
.feature h3{font:500 17.5px "Ubuntu",sans-serif;letter-spacing:-0.2px;color:var(--heading-blue);white-space:nowrap}
.feature-art{position:absolute;border-radius:6px}
.feature p{position:absolute;font:400 12.2px/18px "Arimo",sans-serif;color:var(--body-blue);text-align:justify}
.read-more{position:absolute;top:151px;width:80px;height:23px;border-radius:4px;background:var(--soft-green);color:var(--white);font:400 14px "Arimo",sans-serif;text-align:center;line-height:23px}
.divider{position:absolute;top:572px;width:1px;height:166px;background:#e2e2e2}

.site-footer{position:absolute;left:0;top:762px;width:1200px;height:240px;background:var(--footer-bg)}
.footer-col{position:absolute;top:28px}
.footer-col h4{font:500 14px "Ubuntu",sans-serif;letter-spacing:-0.2px;color:#444;margin-bottom:16px}
.footer-col li{list-style:none;font:400 12.5px "Arimo",sans-serif;color:var(--footer-text);height:24px;padding-left:2px}
.help-title{position:absolute;right:88px;top:22px;font:400 26px "Ubuntu",sans-serif;color:var(--heading-blue);white-space:nowrap}
.phone{position:absolute;right:88px;top:72px;font:400 18px "Ubuntu",sans-serif;color:var(--link-blue);display:flex;align-items:center;gap:8px;white-space:nowrap}
.social-tiles{position:absolute;right:90px;top:132px;display:flex;gap:3px}
.social-tiles span{width:45px;height:45px;border-radius:5px;background:linear-gradient(#8fb3de,#3c6aa8)}
.legal{position:absolute;left:90px;top:167px;font:400 12px "Arimo",sans-serif;color:var(--footer-text);display:flex;white-space:nowrap}
.legal nav{margin-left:19px;color:var(--link-blue)}
.legal nav i{font-style:normal;padding:0 5px;color:#666}
</style>
</head>
<body>

<header>
  <div class="top-bar">
    <a class="social-button follow-button" href="#">FOLLOW US ON <span class="brand">Chirpline</span></a>
    <a class="social-button connect-button" href="#">Log in with <span class="brand">Facebase</span></a>
    <div class="search-field">Search
      <svg width="18" height="18" viewBox="0 0 18 18"><circle cx="7" cy="7" r="5" fill="none" stroke="#fff" stroke-width="1.8"/><line x1="11" y1="11" x2="16" y2="16" stroke="#fff" stroke-width="2"/></svg>
    </div>
  </div>

  <div class="site-header">
    <div class="wordmark"><span class="wordmark-dot"></span>Kerjaloo</div>
    <p class="tagline">Get just about anything done by safe, reliable, awesome people.</p>
    <div class="email-input">Enter Email Address</div>
    <a class="start-button" href="#">Get Started</a>
  </div>

  <nav class="main-nav">
    <a class="nav-item current" href="#">HOW IT WORKS</a>
    <span class="nav-sep" style="left:222px">|</span>
    <a class="nav-item" href="#" style="left:244px">SIGN UP</a>
    <span class="nav-sep" style="left:313px">|</span>
    <a class="nav-item" href="#" style="left:335px">LOGIN</a>
    <span class="nav-sep" style="left:392px">|</span>
    <a class="nav-item" href="#" style="left:414px">BECOME A KERJALOO</a>
    <a class="help-button" href="#">
      <svg width="28" height="28" viewBox="0 0 28 28"><circle cx="14" cy="14" r="13" fill="#2f8ee0"/><text x="14" y="20" text-anchor="middle" font-family="Ubuntu,sans-serif" font-weight="700" font-size="17" fill="#fff">?</text></svg>HELP</a>
    <a class="tell-button" href="#">
      <svg width="28" height="28" viewBox="0 0 28 28"><circle cx="14" cy="14" r="13" fill="#9ad64a"/><path d="M7 12h8V7l7 7-7 7v-5H7z" fill="#fff"/></svg>TELL A FRIEND</a>
  </nav>
</header>

<main>
  <div class="hero-photo" role="img" aria-label="Photo of four smiling friends holding colourful shopping bags">
    <div class="slider-dots"><span></span><span></span><span></span><span></span></div>
  </div>

  <aside class="browse-panel">
    <h2>BROWSE TASKS</h2>
    <ul class="task-list">
      <li>Lorem Ipsum</li><li>Lorem Ipsum</li><li>Lorem Ipsum</li><li>Lorem Ipsum</li><li>Lorem Ipsum</li><li>Lorem Ipsum</li><li>Lorem Ipsum</li><li>Lorem Ipsum</li><li>Lorem Ipsum</li>
    </ul>
  </aside>

  <section class="feature" style="left:86px">
    <h3>HOW KERJALOO WORKS</h3>
    <div class="feature-art" style="left:2px;top:45px;width:106px;height:78px;background:linear-gradient(#3e7a55,#2a5a3d)" role="img" aria-label="Illustration of a chalkboard with a chef hat and bread"></div>
    <p style="left:118px;top:44px;width:185px">Lorem Ipsum is simply dummy text of the printing and typesetting industry. Lorem Ipsum has been the industry's standard dummy text specimen book.</p>
    <a class="read-more" href="#" style="left:117px">read more</a>
  </section>
  <div class="divider" style="left:409px"></div>

  <section class="feature" style="left:428px">
    <h3>SAFETY IS TASK #1</h3>
    <div class="feature-art" style="left:4px;top:41px;width:82px;height:82px;background:linear-gradient(#3aa6ea,#0f6fb8)" role="img" aria-label="Blue protection badge icon"></div>
    <p style="left:122px;top:44px;width:205px">Lorem Ipsum is simply dummy text of the printing and typesetting industry. Lorem Ipsum has been the industry's standard dummy text book.</p>
    <a class="read-more" href="#" style="left:123px">read more</a>
  </section>
  <div class="divider" style="left:775px"></div>

  <section class="feature" style="left:798px">
    <h3>KERJALOO FOR BUSINESS</h3>
    <div class="feature-art" style="left:6px;top:40px;width:86px;height:86px;background:linear-gradient(135deg,#f0f0f0,#2f63a8)" role="img" aria-label="Illustration of a figure climbing a blue bar chart"></div>
    <p style="left:102px;top:44px;width:205px">Lorem Ipsum is simply dummy text of the printing and typesetting industry. Lorem Ipsum has been the industry's standard dummy text book.</p>
    <a class="read-more" href="#" style="left:102px">read more</a>
  </section>
</main>

<footer class="site-footer">
  <div class="footer-col" style="left:88px">
    <h4>ABOUT KERJALOO</h4>
    <ul><li>Sign up / Log in</li><li>How it Works</li><li>Meet the Kerjaloo</li><li>Become a Kerjaloo</li></ul>
  </div>
  <div class="footer-col" style="left:345px">
    <h4>GREAT DEALS</h4>
    <ul><li>Refer a friend</li><li>Gift cards</li><li>Kerjaloo for Business</li></ul>
  </div>
  <div class="footer-col" style="left:586px">
    <h4>POPULAR CITIES</h4>
    <ul><li>Singapore</li><li>Australia</li><li>Malaysia</li><li>Phillipines</li></ul>
  </div>

  <p class="help-title">Need Help? Let’s Talk it Out</p>
  <p class="phone">
    <svg width="16" height="16" viewBox="0 0 24 24"><path d="M6.6 10.8a15 15 0 0 0 6.6 6.6l2.2-2.2a1 1 0 0 1 1-.25 11.4 11.4 0 0 0 3.6.57 1 1 0 0 1 1 1V20a1 1 0 0 1-1 1A17 17 0 0 1 3 4a1 1 0 0 1 1-1h3.5a1 1 0 0 1 1 1c0 1.250.2 2.45.57 3.57a1 1 0 0 1-.25 1z" fill="#3d6aa0"/></svg>
    (555) 014 2290</p>
  <div class="social-tiles" aria-label="Social links"><span title="Facebase"></span><span title="Chirpline"></span></div>

  <div class="legal">
    <span>Copyright © 2012 Kerjaloo.</span>
    <nav>About Us<i>|</i>Team<i>|</i>Careers<i>|</i>Press<i>|</i>Store<i>|</i>Blog<i>|</i>FAQ<i>|</i>Privacy Policy<i>|</i>Terms of Use</nav>
  </div>
</footer>

</body>
</html>
```